NZ First of it's kind solutions directory and marketplace for busy Mums needs a business card design

We need a business card design for our new nationwide business in NZ (long term plans to go global). We provide solutions to the everyday challenges that busy Mums face by connecting them with quality communities and suppliers of carefully selected, relevant products and services. We sell direct via our online marketplace. The final design should communicate our values of inclusivity, quality and smart solutions. Colours should incorporate our logo colour palette of #477077 and #6ba8b2. Our website is at https://www.brightnestmums.example

Target Market(s)

busy Mums, Age 28 – 50, female, income over $100K, location main centres NZ primarily but NZ wide. Is likely juggling work or career with a young family. Probably had hobbies which have fallen by the wayside.
-Wants to succeed in her chosen career without compromising on family life
-to successfully juggle her career without feeling like she is compromising her children
- Is time poor, something always has to give and it’s generally her health (she’ll stay up late, get stressed)
- probably ex corporate or professional career. Has discretional income

Industry/Entity Type

Business

Contact Information for Business Card

Lena Forbisher, Founder, BrightNestMums.example (Strapline Tap; Gather; Sorted), 47 Kowhai Terrace, Ellerslie, Auckland 1051, New Zealand. Mob: 021 483 517 Ph: +64 (0)9 571 4860

Font styles to use
Other font styles liked:
• Raleway, and/or Architects Daughter

Colors
00a990
33b8a4
86cfc6
cfeae6

Requirements
Must have
• the above details, streamline. the logo and colours associated with those logos
Should not have
• foil or metallic colours

```html
<!DOCTYPE html>
<html lang="en">
<head>
<meta charset="utf-8">
<title>BrightNestMums – Business Card</title>
<link rel="stylesheet" href="https://fonts.googleapis.com/css2?family=Roboto:ital,wght@0,400;0,500;0,700;1,400&display=swap">
<style>
  :root {
    --brand-dark: #477077;
    --brand-panel: #3f5f68;
    --brand-light: #6ba8b2;
    --paper: #f7f7f7;
    --backdrop: #e4e4e4;
    --ink-light: #ffffff;
    --ink-muted: #5a5a5a;
    --shadow: 0 3px 6px rgba(0,0,0,0.22);
  }
  * { box-sizing: border-box; margin: 0; padding: 0; }
  html, body {
    width: 1200px; height: 576px; overflow: hidden;
    background: var(--backdrop);
    font-family: "Roboto", Arial, sans-serif;
  }
  .canvas { position: relative; width: 1200px; height: 576px; }
  .card {
    position: absolute; top: 138px;
    width: 484px; height: 292px;
    border-radius: 14px;
    background: var(--paper);
    box-shadow: var(--shadow);
    overflow: hidden;
  }
  .card--front { left: 82px; }
  .card--back { left: 602px; }

  /* Front */
  .front-mark {
    position: absolute; left: 50%; top: 74px;
    width: 56px; height: 56px; margin-left: -28px;
    border-radius: 50%; background: var(--brand-dark);
  }
  .wordmark {
    font-weight: 500; color: var(--brand-dark);
    letter-spacing: -0.5px; white-space: nowrap;
  }
  .front-wordmark {
    position: absolute; left: 0; right: 0; top: 162px;
    text-align: center; font-size: 35px; line-height: 44px;
  }
  .strapline {
    font-size: 10.5px; letter-spacing: 4px; color: var(--ink-muted);
    white-space: nowrap; text-transform: uppercase;
  }
  .strapline .divider { color: var(--brand-light); padding: 0 4px; }
  .front-strapline {
    position: absolute; left: 0; right: 0; top: 207px; text-align: center;
  }

  /* Back */
  .back-panel { position: absolute; inset: 0; width: 484px; height: 292px; }
  .contact-name {
    position: absolute; left: 24px; top: 14px;
    font-size: 19px; font-weight: 700; color: var(--ink-light);
  }
  .contact-role {
    position: absolute; left: 25px; top: 39px;
    font-size: 11px; font-style: italic; color: var(--ink-light);
  }
  .contact-address {
    position: absolute; left: 25px; top: 157px;
    font-size: 12px; line-height: 18px; color: var(--ink-light);
  }
  .contact-list {
    position: absolute; left: 25px; top: 202px; list-style: none;
    font-size: 12px; line-height: 18.5px; color: var(--ink-light);
  }
  .contact-list li { display: flex; align-items: center; gap: 7px; }
  .contact-list svg { width: 10px; height: 10px; flex: none; }
  .back-mark {
    position: absolute; left: 322px; top: 130px;
    width: 26px; height: 26px; border-radius: 50%;
    background: var(--brand-dark);
  }
  .back-brand {
    position: absolute; left: 420px; top: 146px;
    transform: translate(-50%, -50%) rotate(-90deg);
    text-align: center;
  }
  .back-wordmark { font-size: 34px; line-height: 38px; display: block; }
  .back-strapline { display: block; font-size: 9.5px; letter-spacing: 3.6px; margin-top: 2px; }
</style>
</head>
<body>
<main class="canvas">
  <section class="card card--front" aria-label="Business card front">
    <span class="front-mark" aria-hidden="true"></span>
    <div class="wordmark front-wordmark">BrightNestMums</div>
    <div class="strapline front-strapline">Tap<span class="divider">|</span>Gather<span class="divider">|</span>Sorted</div>
  </section>

  <section class="card card--back" aria-label="Business card back">
    <svg class="back-panel" viewBox="0 0 484 292" aria-hidden="true">
      <path d="M0 0 H290 Q232 146 284 292 H0 Z" fill="var(--brand-light)"/>
      <path d="M0 0 H284 Q226 146 278 292 H0 Z" fill="var(--brand-panel)"/>
    </svg>
    <h1 class="contact-name">Lena Forbisher</h1>
    <p class="contact-role">Founder</p>
    <address class="contact-address">47 Kowhai Terrace, Ellerslie,<br>Auckland 1051, New Zealand</address>
    <ul class="contact-list">
      <li><svg viewBox="0 0 10 10"><rect x="2.5" y="0.5" width="5" height="9" rx="1" fill="none" stroke="#fff"/><circle cx="5" cy="7.6" r="0.7" fill="#fff"/></svg>021 483 517</li>
      <li><svg viewBox="0 0 10 10"><path d="M1 4 Q5 0 9 4 L8 5 L6.5 4 V3.2 Q5 2.7 3.5 3.2 V4 L2 5 Z" fill="#fff"/><rect x="2" y="5.5" width="6" height="3.5" rx="0.6" fill="#fff"/></svg>+64 (0)9 571 4860</li>
      <li><svg viewBox="0 0 10 10"><rect x="0.5" y="2" width="9" height="6" fill="none" stroke="#fff"/><path d="M0.5 2 L5 5.5 L9.5 2" fill="none" stroke="#fff"/></svg>www.BrightNestMums.example</li>
      <li><svg viewBox="0 0 10 10"><circle cx="5" cy="5" r="4.3" fill="none" stroke="#fff"/><ellipse cx="5" cy="5" rx="1.8" ry="4.3" fill="none" stroke="#fff" stroke-width="0.8"/><path d="M0.7 5 H9.3" stroke="#fff" stroke-width="0.8"/></svg>lenaforbisher@brightnestmums.example</li>
    </ul>
    <span class="back-mark" aria-hidden="true"></span>
    <div class="back-brand">
      <span class="wordmark back-wordmark">BrightNestMums</span>
      <span class="strapline back-strapline">Tap<span class="divider">|</span>Gather<span class="divider">|</span>Sorted</span>
    </div>
  </section>
</main>
</body>
</html>
```